IT consulting company looking for a modern business design for a website and a new logo

We are the IT-consulting company VelmaTrix from Germany and need a new and modern business website and a new logo. We are specialized in output management. Our services include business analysis, outsourcing, development, training and project leading. We wish for a design with nature pictures (mountains, lakes, rivers, forests, etc.) for our company with the colors green and blue. If it is possible, a slow-mo video of a nature scene. The design should be responsive and the menu should change to a hamburger menu. The following are: • Services / Solutions 1. Output Management 2. Outsourcing 3. Development 4. Business Analyst 5. Training • Partners • Careers • About Us 1. Project A 2. Project B 3. Project C • Contact Notes for the following categories: For "Services / Solutions" we want to conclude some contents from all the sub-points and sub-points below. Additionally, we would like to see some sub-point under "Services / Solutions". For Output Management: "5 Benefits of Output Management Systems (OMS) - OMS Simplifies and Accelerates External Communication - Helps Reduce Communication Mistakes - Provides Customers With Fast and Secure Responses to your questions - Employees can focus on the essential as they can access prepared templates - Companies get complete transparency about their communication "The point" partner does not have sub-points. The content here is a quote and the logo from the company Brel. For now, just placeholders on this site. The next point wants to be "career" without sub-point and wants to contain some text. Carrer options wants to be listed here. Next point wants to be "About us", where we need sub-points which we do not know exactly at this moment, but they will contain text. By clicking directly on "About us" we want to include pictures and texts about 6 employees for which we only need placeholders at the moment. The last point wants to be "contact", where customers can send us messages. The main page should include a story about our company, which can be a placeholder for now. For reference, designs have a look at: https://brelvanto.de/ https://www.tarnopix.com/ https://www.pldrive.de/ We prefer WordPress designs, created with the plugin ELEMENTOR, so that we can easily edit the content by ourselves. The final design should look professional, competent and modern.

Target Market(s)

With our website, we want to reach the following target groups. <br> <br> <br> <br> <br> <br> <br> <br> <br> <br> <br> <br> <br> <br> <br> <br> <br> <br> <br> <br> <br> <br> <br> <br> <br> <br> <br> <br> <br> <br> <br> <br> <br> <br> <br> <br> <br> <br> <br> <br> <br> <br> <br> <br> <br> <br> <br> <br> <br>

Industry/Entity Type

Consulting

Logo Text

(optionally) VelmaTrix

Font styles to use
Sans Serif

Colors

Designer to choose colors to be used in the design.

Requirements
Must have
• 1. Outsourcing 3. Development 4. Business Analyst 5. Training • Partners • Careers • About Us 1. Project A 2. Project B 3. Project C • Contact The above-mentioned background picture with nature motifs (mountains, lakes, rivers, forests, etc.). WordPress design in primary colors blue and green.
Nice to have
• ELEMENTOR template. Effects for the background pictures. Counter of all successful projects for Output Management, Business Analyst and Training

```html
<!DOCTYPE html>
<html lang="de">
<head>
<meta charset="utf-8">
<title>VelmaTrix – IT Consulting</title>
<link href="https://fonts.googleapis.com/css2?family=Poppins:wght@400;500;600;700&display=swap" rel="stylesheet">
<style>
:root{
  --blue:#0d5aa7;
  --blue-dark:#0a4a8c;
  --green:#7dbb2e;
  --ink:#222;
  --muted:#555;
  --grey-band:#e8eaee;
  --footer:#1c3150;
}
*{margin:0;padding:0;box-sizing:border-box}
html,body{width:1200px;height:4295px;overflow:hidden}
body{font-family:"Poppins",sans-serif;color:var(--ink);background:#fff;position:relative}
section,header,footer{position:relative;width:1200px;overflow:hidden}
.abs{position:absolute}
.center-x{left:0;right:0;text-align:center}
.btn{position:absolute;background:var(--green);color:#fff;border-radius:20px;font-size:16px;font-weight:500;display:flex;align-items:center;justify-content:center}
.title{position:absolute;left:0;right:0;text-align:center;font-size:36px;font-weight:600;line-height:44px;color:var(--blue)}
.title .g{color:var(--green)}
.rule{position:absolute;left:560px;width:80px;height:2px;background:#bbb}

/* header */
.topline{height:7px;background:#d9d9d9}
.site-header{height:93px;background:#fff}
.brand{position:absolute;left:142px;top:26px;display:flex;align-items:center;gap:12px}
.brand-dot{width:34px;height:34px;border-radius:50%;border:3px solid var(--blue)}
.brand-name{font-size:32px;font-weight:600;color:var(--blue);line-height:36px;letter-spacing:1px}
.nav{position:absolute;top:40px;display:flex;font-size:14px;font-weight:500}
.nav a{position:absolute;white-space:nowrap;color:var(--ink);text-decoration:none}
.nav a.active{color:var(--green)}
.phone-pill{position:absolute;left:888px;top:35px;width:172px;height:31px;border-radius:16px;background:var(--green);color:#fff;font-size:16px;font-weight:500;display:flex;align-items:center;justify-content:center;gap:8px}

/* hero */
.hero{height:553px}
.hero-photo{position:absolute;inset:0;background:linear-gradient(90deg,#1b1d22 0%,#3a4048 35%,#7d8690 60%,#c9ced2 100%)}
.hero-text{position:absolute;left:143px;top:172px;font-size:37px;font-weight:600;line-height:52px;color:#fff}

/* about */
.about{height:430px}
.mission{position:absolute;left:0;right:0;top:155px;text-align:center;font-size:14px;font-weight:600;line-height:20px}
.about-copy{position:absolute;left:148px;width:904px;top:183px;text-align:center;font-size:14px;line-height:25.5px;color:#333}

/* services */
.services{height:447px}
.services-bg{position:absolute;inset:0;background:linear-gradient(180deg,#3b5b7c 0%,#4e6f86 45%,#2f4d63 100%)}
.services .title{color:#fff}
.svc-label{position:absolute;color:#fff;font-size:19px;line-height:24px;white-space:nowrap}

/* vision */
.vision{height:633px}
.v-card{position:absolute;top:182px;width:276px;height:276px;border-radius:50%;background:radial-gradient(circle at 50% 45%,#fafafa 0%,#ececec 70%,#e0e0e0 100%);text-align:center}
.v-card.feature{background:var(--blue);color:#fff;width:284px;height:284px;top:178px;box-shadow:0 0 0 6px #fff,0 0 0 8px var(--blue)}
.v-head{position:absolute;left:0;right:0;top:105px;font-size:18px;font-weight:500;color:var(--blue)}
.v-card.feature .v-head{color:#fff}
.v-sub{position:absolute;left:0;right:0;top:130px;font-size:12px;color:#444}
.v-card.feature .v-sub{color:#fff}
.v-body{position:absolute;left:30px;right:30px;top:162px;font-size:12.5px;line-height:20px;color:#555}
.v-card.feature .v-body{color:#fff}
.v-icon{position:absolute;left:50%;top:38px;transform:translateX(-50%)}

/* benefits */
.benefits{height:534px;background:var(--grey-band)}
.b-head{position:absolute;left:143px;font-size:30px;line-height:36px;font-weight:400}
.b-list{position:absolute;left:143px;top:193px;width:560px;font-size:13.5px;line-height:21px;color:#333}
.b-list p{margin-bottom:12.5px}

/* reviews */
.reviews{height:356px}
.r-photo{position:absolute;top:163px;width:108px;height:108px;background:linear-gradient(135deg,#cfd6de,#8b97a6)}
.r-quote{position:absolute;top:160px;font-size:46px;line-height:46px;color:#c9c9c9;font-weight:700}
.r-text{position:absolute;top:190px;width:360px;font-size:12.5px;line-height:22px;color:#333;white-space:nowrap}
.r-name{position:absolute;top:243px;font-size:14px;color:#222}
.arrow{position:absolute;width:34px;height:34px;border-radius:50%;background:#fff;box-shadow:0 1px 5px rgba(0,0,0,.25);display:flex;align-items:center;justify-content:center}

/* team */
.team{height:577px;background:var(--grey-band)}
.t-member{position:absolute;top:160px;width:220px;text-align:center}
.t-photo{width:124px;height:124px;border-radius:50%;margin:0 auto;border:3px solid var(--blue);box-shadow:inset 0 0 0 4px #fff;background:linear-gradient(180deg,#9aa3ad,#4a525c)}
.t-name{margin-top:30px;font-size:16px;font-weight:500;color:var(--blue);line-height:20px}
.t-role{font-size:12.5px;color:#444;line-height:18px}
.t-body{margin-top:12px;font-size:13px;line-height:20px;color:#444}

/* partners */
.partners{height:377px}
.partners .title{font-weight:400}
.p-box{position:absolute;top:168px;width:122px;height:72px;border:1px solid #ddd;background:#fff;box-shadow:0 1px 4px rgba(0,0,0,.12);display:flex;align-items:center;justify-content:center;font-size:17px;font-weight:600;color:#444}
.p-dot{position:absolute;top:266px;width:22px;height:22px;border-radius:50%;border:1px solid #bbb;background:#fff}

/* footer */
.site-footer{height:288px}
.footer-bg{position:absolute;inset:0;background:linear-gradient(180deg,#23395a 0%,#1c3150 60%,#16283f 100%)}
.f-col{position:absolute;top:37px;color:#fff;font-size:12.5px}
.f-title{color:var(--green);font-size:14px;line-height:22px}
.f-title::after{content:"";display:block;width:32px;height:1px;background:#fff;margin-top:8px}
.f-links{margin-top:14px;line-height:26.5px;font-size:12.5px}
.f-row{position:absolute;display:flex;gap:12px;font-size:12.5px;line-height:20px}
.f-input{position:absolute;left:0;top:96px;width:192px;height:30px;border-radius:15px;background:#fff;color:#999;font-size:11px;padding-left:14px;line-height:30px}
.f-sub{position:absolute;left:0;top:136px;width:123px;height:29px;border-radius:15px;background:var(--green);color:#fff;font-size:15px;display:flex;align-items:center;justify-content:center}
.f-social{position:absolute;top:90px;width:24px;height:24px;border-radius:50%;background:#fff}
.copyright{position:absolute;left:0;right:0;top:256px;text-align:center;color:#fff;font-size:12px;line-height:20px}
.f-divider{position:absolute;left:0;right:0;top:246px;height:1px;background:rgba(255,255,255,.15)}
</style>
</head>
<body>

<div class="topline"></div>
<header class="site-header">
  <div class="brand"><span class="brand-dot"></span><span class="brand-name">VelmaTrix</span></div>
  <nav class="nav">
    <a class="active" style="left:465px">Home</a>
    <a style="left:533px">About Us</a>
    <a style="left:622px">Services</a>
    <a style="left:707px">Careers</a>
    <a style="left:789px">Contact Us</a>
  </nav>
  <div class="phone-pill">
    <svg width="18" height="18" viewBox="0 0 24 24"><circle cx="12" cy="12" r="10.5" fill="none" stroke="#fff" stroke-width="1.6"/><path d="M8.5 7c.6-.6 1.4-.5 1.8.2l.8 1.4c.3.5.2 1.1-.2 1.4l-.6.5c.5 1.2 1.5 2.3 2.8 2.9l.5-.6c.4-.4 1-.5 1.4-.2l1.4.8c.7.4.8 1.2.2 1.8l-.7.7c-2.7 1-7.7-4-6.7-6.7z" fill="#fff"/></svg>
    123.456.7890
  </div>
</header>

<section class="hero">
  <div class="hero-photo" role="img" aria-label="Team meeting in a bright office, a consultant presenting charts on a screen"></div>
  <h1 class="hero-text">We Are Specialized<br>In Output<br>Management</h1>
  <div class="btn" style="left:142px;top:348px;width:150px;height:30px;font-size:16px">We Can Help</div>
</section>

<section class="about">
  <h2 class="title" style="top:78px;font-size:40px;letter-spacing:1px">About Velma<span class="g">Trix</span></h2>
  <div class="rule" style="top:134px"></div>
  <p class="mission">Our mission is dipiscing elit, sed diam nonummy nibh euismod tincidunt ut.</p>
  <p class="about-copy">Lorem ipsum dolor sit amet, consectetuer adipiscing elit, sed diam nonummy nibh euismod tincidunt ut laoreet dolore magna aliquam erat volutpat. Ut wisi enim ad minim veniam, quis nostrud exerci tation ullamcorper suscipit lobortis nisl ut aliquip ex ea commodo consequat. Duis autem vel eum iriure dolor in hendrerit in vulputate velit esse molestie consequat, vel illum dolore eu feugiat nulla facilisis at vero eros et accumsan et iusto odio dignissim qui blandit praesent luptatum zzril delenit augue duis dolore te feugait nulla facilisi.</p>
  <div class="btn" style="left:530px;top:320px;width:138px;height:30px">Read More</div>
</section>

<section class="services">
  <div class="services-bg" role="img" aria-label="Misty mountain range with forested slopes in blue tones"></div>
  <h2 class="title" style="top:68px;font-size:34px">Our <span class="g">Services</span></h2>
  <div class="rule" style="top:113px;background:#fff;width:70px;left:565px"></div>

  <svg class="abs" style="left:0;top:0" width="1200" height="447" viewBox="0 0 1200 447">
    <path d="M430 447 A153 153 0 0 1 736 447 Z" fill="#fff"/>
    <path d="M430 447 A153 153 0 0 1 736 447" fill="none" stroke="#0d5aa7" stroke-width="5"/>
    <g fill="#7dbb2e" stroke="#fff" stroke-width="2">
      <circle cx="583" cy="294" r="6"/><circle cx="480" cy="332" r="6"/><circle cx="438" cy="400" r="6"/>
      <circle cx="686" cy="332" r="6"/><circle cx="728" cy="400" r="6"/>
    </g>
    <g stroke="#7dbb2e" stroke-width="3" fill="#fff">
      <circle cx="583" cy="225" r="36"/>
      <circle cx="430" cy="275" r="36"/>
      <circle cx="735" cy="275" r="36"/>
      <circle cx="793" cy="377" r="36"/>
    </g>
    <circle cx="377" cy="377" r="36" fill="#7dbb2e" stroke="#fff" stroke-width="3"/>
    <g fill="none" stroke="#0d5aa7" stroke-width="2.5">
      <path d="M571 238 l20-24 l6-2 l-2 6 l-24 20 z"/><circle cx="590" cy="232" r="6"/><path d="M575 227 l-6 2 l-3 6 M582 237 l-2 6 l-6 3"/>
    </g>
    <g fill="none" stroke="#0d5aa7" stroke-width="2.2">
      <circle cx="430" cy="275" r="8"/><circle cx="430" cy="275" r="17" stroke-dasharray="5 4"/>
    </g>
    <g fill="#0d5aa7">
      <rect x="720" y="280" width="6" height="12"/><rect x="729" y="272" width="6" height="20"/><rect x="738" y="265" width="6" height="27"/>
      <circle cx="750" cy="264" r="4"/><rect x="746" y="270" width="8" height="22"/>
    </g>
    <g fill="none" stroke="#0d5aa7" stroke-width="2.2">
      <rect x="788" y="361" width="22" height="18"/><circle cx="780" cy="367" r="4"/><path d="M777 392 v-16 h7 l6-4 M783 392 v-10"/>
    </g>
    <g fill="none" stroke="#fff" stroke-width="2.2">
      <rect x="362" y="364" width="26" height="18"/><path d="M370 388 h10 M375 382 v6"/><rect x="384" y="372" width="9" height="14" fill="#7dbb2e"/>
    </g>
    <circle cx="583" cy="365" r="17" fill="none" stroke="#0d5aa7" stroke-width="3"/>
  </svg>

  <div class="svc-label" style="left:0;right:0;top:152px;text-align:center">Entwicklung</div>
  <div class="svc-label" style="right:818px;top:260px">Outsourcing</div>
  <div class="svc-label" style="right:872px;top:363px">Output Management</div>
  <div class="svc-label" style="left:782px;top:257px">Business Analyst</div>
  <div class="svc-label" style="left:837px;top:358px">Schulungen</div>
  <div class="abs center-x" style="top:394px;font-size:33px;font-weight:600;color:var(--blue);line-height:40px;letter-spacing:1px">VelmaTrix</div>
</section>

<section class="vision">
  <h2 class="title" style="top:85px;font-size:30px">Our <span class="g">Vision</span></h2>

  <div class="v-card" style="left:190px">
    <svg class="v-icon" width="56" height="56" viewBox="0 0 56 56"><circle cx="24" cy="24" r="13" fill="none" stroke="#444" stroke-width="2"/><circle cx="24" cy="24" r="7" fill="none" stroke="#7dbb2e" stroke-width="2"/><path d="M33 33 l12 12" stroke="#444" stroke-width="3"/><path d="M24 4 v4 M8 10 l3 3 M40 10 l-3 3" stroke="#7dbb2e" stroke-width="2"/></svg>
    <div class="v-head">Discover</div>
    <div class="v-sub">Evaluate new geos</div>
    <div class="v-body">Ut wisi enim ad minim veniam, quis nostrud exerci tatio<br>Ut wisi enim ad minim.</div>
  </div>

  <div class="v-card feature" style="left:453px">
    <svg class="v-icon" width="58" height="58" viewBox="0 0 58 58" fill="none" stroke="#fff" stroke-width="3"><path d="M4 16 V4 H16 M42 4 H54 V16 M54 42 V54 H42 M16 54 H4 V42"/><path d="M8 8 l12 12 M50 8 l-12 12 M50 50 l-12-12 M8 50 l12-12" stroke="#7dbb2e"/></svg>
    <div class="v-head">Expand</div>
    <div class="v-sub">Set up new geos</div>
    <div class="v-body">Ut wisi enim ad minim veniam, quis nostrud exerci tatio<br>Ut wisi enim ad minim.</div>
  </div>

  <div class="v-card" style="left:717px">
    <svg class="v-icon" width="60" height="58" viewBox="0 0 60 58" fill="#444"><rect x="28" y="0" width="4" height="58" fill="#7dbb2e"/><rect x="2" y="8" width="22" height="4"/><rect x="36" y="8" width="22" height="4"/><rect x="10" y="20" width="14" height="4"/><rect x="36" y="20" width="14" height="4"/><rect x="2" y="32" width="22" height="4"/><rect x="36" y="32" width="22" height="4"/><rect x="14" y="44" width="10" height="4"/><rect x="36" y="44" width="10" height="4"/></svg>
    <div class="v-head">Align</div>
    <div class="v-sub">Ensure success</div>
    <div class="v-body">Ut wisi enim ad minim veniam, quis nostrud exerci tatio<br>Ut wisi enim ad minim.</div>
  </div>

  <div class="btn" style="left:517px;top:512px;width:165px;height:38px">Call Us Today</div>
</section>

<section class="benefits">
  <h2 class="b-head" style="top:106px;color:var(--blue)">5 Vorteile von</h2>
  <h2 class="b-head" style="top:142px;color:var(--green)">Output Management Systemen (OMS)</h2>
  <div class="b-list">
    <p>OMS vereinfacht und beschleunigt die Kommunikation mit Außen.</p>
    <p>Hilft dabei Fehler bei der Kommunikation zu reduzieren.</p>
    <p>Kunden erhalten schnell und sicher antworten auf Ihre Fragen.</p>
    <p>Mitarbeiter können sich auf das wesentliche konzentrieren, da sie auf vorbereitete Vorlagen zurückgreifen können.</p>
    <p>Unternehmen erhalten vollständige Transparenz über Ihre Kommunikation</p>
  </div>
  <div class="btn" style="left:143px;top:385px;width:164px;height:37px">Call Us Today</div>
  <svg class="abs" style="left:700px;top:130px" width="310" height="330" viewBox="0 0 310 330"><circle cx="153" cy="157" r="147" fill="#0d5aa7"/></svg>
  <div class="abs" role="img" aria-label="Smiling businesswoman with long hair and folded arms" style="left:738px;top:70px;width:232px;height:392px;border-radius:116px 116px 60px 60px;background:linear-gradient(180deg,#6b4a36 0%,#a98670 35%,#e9e4df 65%,#8a6652 100%)"></div>
</section>

<section class="reviews">
  <h2 class="title" style="top:64px">Happy Customer <span class="g">Reviews</span></h2>
  <div class="rule" style="top:119px"></div>

  <div class="r-photo" style="left:138px" role="img" aria-label="Portrait of a grey-haired client in a suit"></div>
  <div class="r-quote" style="left:256px">&ldquo;</div>
  <p class="r-text" style="left:260px">Lorem ipsum dolor smet, consectetuer adipiscing<br>elit, sed diam nonumtincidunt ut laoreet....<span style="color:var(--blue)">[+]</span></p>
  <div class="r-name" style="left:260px">Lorem Ispum</div>

  <div class="r-photo" style="left:612px" role="img" aria-label="Portrait of a smiling client with glasses"></div>
  <div class="r-quote" style="left:731px">&ldquo;</div>
  <p class="r-text" style="left:735px">Lorem ipsum dolor smet, consectetuer adipiscing<br>elit, sed diam nonumtincidunt ut laoreet....<span style="color:var(--blue)">[+]</span></p>
  <div class="r-name" style="left:735px">Lorem Ispum</div>

  <div class="arrow" style="left:83px;top:208px"><svg width="10" height="10" viewBox="0 0 10 10"><path d="M7 1 L2 5 L7 9 Z" fill="#999"/></svg></div>
  <div class="arrow" style="left:1063px;top:194px"><svg width="10" height="10" viewBox="0 0 10 10"><path d="M3 1 L8 5 L3 9 Z" fill="#999"/></svg></div>
</section>

<section class="team">
  <h2 class="title" style="top:83px;color:var(--green)">Our <span style="color:var(--blue)">Team</span></h2>
  <div class="rule" style="top:134px"></div>

  <div class="t-member" style="left:128px">
    <div class="t-photo" role="img" aria-label="Portrait of Dana Hollister"></div>
    <div class="t-name">Dana Hollister</div><div class="t-role">Head of Operations</div>
    <p class="t-body">Ut wisi enim ad minim veniam, quis nostrUt wisi enim a nostrud exd minim.</p>
  </div>
  <div class="t-member" style="left:363px">
    <div class="t-photo" role="img" aria-label="Portrait of Mei Carrow"></div>
    <div class="t-name">Mei Carrow</div><div class="t-role">Product Lead</div>
    <p class="t-body">Ut wisi enim ad minim veniam, quis nostrUt wisi enim a nostrud exd minim.</p>
  </div>
  <div class="t-member" style="left:598px">
    <div class="t-photo" role="img" aria-label="Portrait of Tobin Vale"></div>
    <div class="t-name">Tobin Vale</div><div class="t-role">CEO</div>
    <p class="t-body">Ut wisi enim ad minim veniam, quis nostrUt wisi enim a nostrud exd minim.</p>
  </div>
  <div class="t-member" style="left:835px">
    <div class="t-photo" role="img" aria-label="Portrait of Anton Kessler"></div>
    <div class="t-name">Anton Kessler</div><div class="t-role">Co-Founder, Advisor</div>
    <p class="t-body">Ut wisi enim ad minim veniam, quis nostrUt wisi enim a nostrud exd minim.</p>
  </div>

  <div class="btn" style="left:518px;top:464px;width:164px;height:38px">Meet Our Team</div>
</section>

<section class="partners">
  <h2 class="title" style="top:81px;font-size:30px">Our <span class="g">Partners</span></h2>
  <div class="p-box" style="left:162px">Sentavo</div>
  <div class="p-box" style="left:308px">Qlimo</div>
  <div class="p-box" style="left:457px">Korvan</div>
  <div class="p-box" style="left:603px">Tessaro</div>
  <div class="p-box" style="left:752px">Nuvari</div>
  <div class="p-box" style="left:898px">Blocktern</div>
  <div class="p-dot" style="left:538px"></div>
  <div class="p-dot" style="left:572px"></div>
</section>

<footer class="site-footer">
  <div class="footer-bg" role="img" aria-label="Dusky city skyline seen from above in dark blue tones"></div>

  <div class="f-col" style="left:143px">
    <div class="f-title">Quick Links</div>
    <div class="f-links">Home<br>About Us<br>Services<br>Careers<br>Contact Us</div>
  </div>

  <div class="f-col" style="left:303px;width:240px;height:200px">
    <div class="f-title">Contact Details</div>
    <div class="f-row" style="left:0;top:50px">
      <svg width="16" height="18" viewBox="0 0 16 18"><path d="M8 1a6 6 0 0 0-6 6c0 4.5 6 10 6 10s6-5.5 6-10a6 6 0 0 0-6-6z" fill="#7dbb2e"/><circle cx="8" cy="7" r="2.3" fill="#1c3150"/></svg>
      <span>Street Name, City Name<br>State Zipcode</span>
    </div>
    <div class="f-row" style="left:0;top:110px">
      <svg width="16" height="16" viewBox="0 0 24 24"><circle cx="12" cy="12" r="10.5" fill="none" stroke="#7dbb2e" stroke-width="2"/><path d="M8.5 7c.6-.6 1.4-.5 1.8.2l.8 1.4c.3.5.2 1.1-.2 1.4l-.6.5c.5 1.2 1.5 2.3 2.8 2.9l.5-.6c.4-.4 1-.5 1.4-.2l1.4.8c.7.4.8 1.2.2 1.8l-.7.7c-2.7 1-7.7-4-6.7-6.7z" fill="#7dbb2e"/></svg>
      <span>123.456.7890</span>
    </div>
    <div class="f-row" style="left:0;top:150px">
      <svg width="16" height="14" viewBox="0 0 16 14"><rect x="1" y="2" width="14" height="10" fill="none" stroke="#7dbb2e" stroke-width="1.5"/><path d="M1 2 L8 8 L15 2" fill="none" stroke="#7dbb2e" stroke-width="1.5"/></svg>
      <span>inquiry@velmatrix.com</span>
    </div>
  </div>

  <div class="f-col" style="left:580px;width:220px;height:200px">
    <div class="f-title">Newsletter Signup</div>
    <p style="position:absolute;top:50px;width:200px;line-height:20px">Lorem Ispum is the dummy text of the industry</p>
    <div class="f-input">enter email address</div>
    <div class="f-sub">Subscribe</div>
  </div>

  <div class="f-col" style="left:853px;width:260px;height:200px">
    <div class="f-title">Follow Us On</div>
    <div class="f-social" style="left:0"></div>
    <div class="f-social" style="left:35px"></div>
    <div class="f-social" style="left:70px"></div>
    <div style="position:absolute;left:-6px;top:140px;display:flex;align-items:center;gap:10px">
      <span style="width:30px;height:30px;border-radius:50%;border:2px solid #fff;display:block"></span>
      <span style="font-size:28px;font-weight:600;line-height:34px;color:#fff;letter-spacing:1px">VelmaTrix</span>
    </div>
  </div>

  <div class="f-divider"></div>
  <p class="copyright">Copyright © 2019 VelmaTrix. All Rights Reserved.</p>
</footer>

</body>
</html>
```